ORU professional cleaner

this professional multi-surface cleaner is intended for professionals.
Powerful degreaser. We would like to focus on the professional side.
We already have a range of disinfectants, and we would like a design close to this range but still distinct. The name is ORU and yhe logo is MOXAglow.the visible part of the label is 55mm and will be affixed to a round bottle with trigger .

Target Market(s)

professional

```html
<!DOCTYPE html>
<html lang="en">
<head>
<meta charset="UTF-8">
<title>ORU Professional Multi-Surface Cleaner – Label</title>
<link rel="stylesheet" href="https://fonts.googleapis.com/css2?family=PT+Sans+Narrow:wght@400;700&display=swap">
<style>
  :root {
    --page-bg: #f5f5f5;
    --brand-red: #d8161f;
    --brand-red-soft: #e03a42;
    --sky-blue: #7fc8ea;
    --sky-pale: #d6ecf8;
    --label-white: #ffffff;
    --ink-dark: #3a0a10;
  }
  * { margin: 0; padding: 0; box-sizing: border-box; }
  html, body {
    width: 900px;
    height: 1200px;
    overflow: hidden;
    background: var(--page-bg);
  }
  .canvas {
    position: relative;
    width: 900px;
    height: 1200px;
  }
  .label {
    position: absolute;
    left: 200px;
    top: 30px;
    width: 500px;
    height: 1140px;
    overflow: hidden;
    background: linear-gradient(180deg, var(--sky-blue) 8%, var(--sky-pale) 38%, var(--label-white) 60%);
    font-family: "PT Sans Narrow", "Arial Narrow", sans-serif;
  }
  .top-band {
    position: absolute;
    left: 0; top: 0;
    width: 100%;
    height: 100px;
    background: var(--brand-red);
    display: flex;
    align-items: center;
    justify-content: center;
  }
  .top-band__text {
    color: var(--label-white);
    font-weight: 700;
    font-size: 62px;
    letter-spacing: 0.5px;
  }
  .usage-icon {
    position: absolute;
    left: 335px;
    top: 150px;
    width: 120px;
    height: 170px;
  }
  .product-name {
    position: absolute;
    left: 40px;
    top: 220px;
    font-weight: 700;
    font-size: 230px;
    line-height: 1;
    color: var(--brand-red);
    -webkit-text-stroke: 5px var(--label-white);
    paint-order: stroke fill;
    letter-spacing: -2px;
  }
  .descriptions {
    position: absolute;
    left: 52px;
    top: 455px;
    list-style: none;
  }
  .descriptions__item {
    color: var(--ink-dark);
    font-weight: 700;
    font-size: 42px;
    line-height: 46px;
    margin-bottom: 10px;
  }
  .descriptions__lang {
    font-size: 33px;
  }
  .bottom-wave {
    position: absolute;
    left: 0;
    top: 860px;
    width: 500px;
    height: 280px;
  }
  .brand {
    position: absolute;
    left: 0;
    top: 960px;
    width: 100%;
    display: flex;
    flex-direction: column;
    align-items: center;
    gap: 14px;
  }
  .brand__dot {
    width: 46px;
    height: 46px;
    border-radius: 50%;
    background: var(--label-white);
  }
  .brand__name {
    color: var(--label-white);
    font-weight: 700;
    font-size: 66px;
    line-height: 1;
  }
</style>
</head>
<body>
<div class="canvas">
  <div class="label">
    <div class="top-band">
      <span class="top-band__text">PROFESSIONAL</span>
    </div>

    <svg class="usage-icon" viewBox="0 0 120 170" role="img" aria-label="Icon of a hand wiping a surface with a cloth">
      <rect x="10" y="40" width="100" height="110" rx="22" fill="var(--brand-red)" stroke="var(--label-white)" stroke-width="4"/>
    </svg>

    <div class="product-name">ORU</div>

    <ul class="descriptions">
      <li class="descriptions__item">MULTI-SURFACE<br>CLEANER <span class="descriptions__lang">FR</span></li>
      <li class="descriptions__item">MULTI-SURFACE<br>CLEANER</li>
      <li class="descriptions__item">MULTI-SURFACE<br>CLEANER <span class="descriptions__lang">DE</span></li>
    </ul>

    <svg class="bottom-wave" viewBox="0 0 500 280" preserveAspectRatio="none" aria-hidden="true">
      <path d="M0 40 C60 -10 120 10 170 40 C220 70 280 70 330 40 C380 10 440 -10 500 40 L500 280 L0 280 Z" fill="var(--brand-red)"/>
    </svg>

    <div class="brand">
      <span class="brand__dot"></span>
      <span class="brand__name">MOXAglow</span>
    </div>
  </div>
</div>
</body>
</html>
```